Brindle Yard Care. The best in the biz

I run a lawn care service that offers full service mowing. 100% satisfaction guarantee. Fast, Friendly, quality service "I am your lawns best friend" I cut residential lawns. I offer a mow package that includes trimming, edging and clean up. Prices very from 20 dollars to 75. I want my logo to stand out. Free estimates

Target Market(s)

Home owners

Industry/Entity Type

Landscaping

Contact Information for Business Card

555-812-4473 tomvale48@quillmail.net Derek. Brindle Yard care

Colors
f37122
9bcb3c
cadf82

Requirements
Must have
• Company name.
• Phone number
• Email
• My services
• images
Nice to have
• A sun that is growing grass.
Should not have
• Incorrect information

```html
<!DOCTYPE html>
<html lang="en">
<head>
<meta charset="utf-8">
<title>Brindle Yard Care – Business Cards</title>
<link rel="stylesheet" href="https://fonts.googleapis.com/css2?family=Montserrat:wght@500&family=Source+Sans+3:ital,wght@0,400;0,600;0,700;1,700&display=swap">
<style>
  :root {
    --brand-green: #17993f;
    --brand-yellow: #f6d100;
    --card-white: #ffffff;
    --backdrop: #ecebe8;
    --ink-light: #ffffff;
  }
  * { margin: 0; padding: 0; box-sizing: border-box; }
  html, body {
    width: 1200px; height: 900px; overflow: hidden;
    background: var(--backdrop);
    font-family: "Source Sans 3", sans-serif;
  }
  .canvas { position: relative; width: 1200px; height: 900px; }

  .card {
    position: absolute;
    box-shadow: 0 6px 18px rgba(0,0,0,0.18);
    overflow: hidden;
  }
  .card--front { left: 77px; top: 33px; width: 590px; height: 365px; background: var(--card-white); }
  .card--back  { left: 388px; top: 505px; width: 567px; height: 352px; background: var(--brand-green); }

  .card__bands { position: absolute; inset: 0; }

  .wordmark {
    position: absolute; left: 0; right: 0;
    display: flex; align-items: center; justify-content: center; gap: 12px;
    font-family: "Montserrat", sans-serif; font-weight: 500;
    letter-spacing: 0.5px; white-space: nowrap;
  }
  .wordmark__dot { width: 30px; height: 30px; border-radius: 50%; flex: none; }
  .card--front .wordmark { top: 98px; font-size: 42px; color: var(--brand-green); }
  .card--front .wordmark__dot { background: var(--brand-yellow); }
  .card--back .wordmark { top: 118px; font-size: 40px; color: var(--ink-light); }
  .card--back .wordmark__dot { background: var(--ink-light); }

  .contact {
    position: absolute; left: 0; right: 0; top: 243px;
    text-align: center; color: var(--ink-light);
  }
  .contact__name { font-size: 21px; font-weight: 600; margin-bottom: 20px; }
  .contact__line {
    display: flex; align-items: center; justify-content: center; gap: 6px;
    font-size: 16px; line-height: 24px;
  }
  .contact__icon { width: 11px; height: 11px; fill: var(--ink-light); }

  .promise {
    position: absolute; left: 0; right: 0; top: 240px;
    text-align: center; color: var(--ink-light);
  }
  .promise__guarantee { font-size: 25px; font-style: italic; font-weight: 700; }
  .promise__values { font-size: 17px; font-weight: 700; margin-top: 14px; word-spacing: 2px; }
</style>
</head>
<body>
<main class="canvas">

  <section class="card card--front" aria-label="Business card front">
    <svg class="card__bands" width="590" height="365" viewBox="0 0 590 365" aria-hidden="true">
      <polygon points="0,200 404,200 380,225 0,225" fill="var(--brand-yellow)"/>
      <polygon points="416,192 590,192 590,365 0,365 0,229 381,229" fill="var(--brand-green)"/>
    </svg>
    <div class="wordmark"><span class="wordmark__dot"></span>Brindle Yard Care</div>
    <div class="contact">
      <p class="contact__name">Derek</p>
      <p class="contact__line">
        <svg class="contact__icon" viewBox="0 0 24 24" aria-hidden="true"><path d="M6.6 10.8a15.2 15.2 0 0 0 6.6 6.6l2.2-2.2a1 1 0 0 1 1-.25 11.4 11.4 0 0 0 3.6.57 1 1 0 0 1 1 1V20a1 1 0 0 1-1 1A17 17 0 0 1 3 4a1 1 0 0 1 1-1h3.5a1 1 0 0 1 1 1c0 1.25.2 2.45.57 3.57a1 1 0 0 1-.25 1z"/></svg>
        555-812-4473
      </p>
      <p class="contact__line">
        <svg class="contact__icon" viewBox="0 0 24 18" aria-hidden="true"><path d="M0 0h24v18H0z M2 2l10 8 10-8" fill="var(--ink-light)"/><path d="M1 1l11 9 11-9" fill="none" stroke="var(--brand-green)" stroke-width="2"/></svg>
        tomvale48@quillmail.net
      </p>
    </div>
  </section>

  <section class="card card--back" aria-label="Business card back">
    <div class="wordmark"><span class="wordmark__dot"></span>Brindle Yard Care</div>
    <div class="promise">
      <p class="promise__guarantee">100% satisfaction guarantee.</p>
      <p class="promise__values">Fast | Friendly | Quality Service</p>
    </div>
  </section>

</main>
</body>
</html>
```